International Clinical Software Company needs a new business card design

We are looking for a new business card design for our company that has recently expanded into the UK market, making us a multinational company.
After having rebranded our website and produced a new style guide, we are looking for a business card that is creative and attention grabbing, while being consistent with the style and colour scheme used on the new website, www.plumvora.example
We produce care management technology for the aged care market, but the main aspect we aim to communicate is the human element of our software, and the way it assists in providing better care for aged people, and stronger relationships between aged people and the staff that care for them.
Our current business card is a dark green with gold text, which makes the text quite difficult to read, not very aesthetically appealing and the colour scheme looks quite dated.
We would like something fresh and modern, that can still be colourful but doesn't use large blocks of dark colour, and uses the colours within our logo.
Something tying in with the leaves that are used in our logo could work quite nicely, along with the Autumn/Fall colours of soft greens, yellows and reds (also in our existing logo). However also happy to look at fresh, completely out of the box ideas we may not have yet considered.
Target Market(s)
The people that receive this business card work in the aged card or health industry and are either corporate/management level staff or clinical (Registered Nurses, care workers etc.)
Industry/Entity Type
Health Product
Contact Information for Business Card
Company Name - BrindlewayCare
Company locations: United Kingdom, Australia, New Zealand
Staff Details:
Staff name: Derek Mallow
Staff job title: Executive Chairman
Staff email: d.mallow@plumvora.example
Office phone number: 01742 918576
Font styles to use
Other font styles liked:
- Calibri
Requirements
Must have
- Must include the BrindlewayCare brand name in it's current font
- Must include logo (3 leaves in gold circle)
- Must include Business Card Details
Nice to have
- Elements of gold
- White space
- Something autumn themed but not too cliched
Should not have
- No blue - used by a major competitor and we would like to differentiate from them
- Large blocks of dark green colour (the green that appears in our leaves on the logo on our current business card is the background colour and it is far too dark)

```html
<!DOCTYPE html>
<html lang="en">
<head>
<meta charset="utf-8">
<title>BrindlewayCare – Business Card</title>
<link rel="stylesheet" href="https://fonts.googleapis.com/css2?family=Open+Sans:wght@300;400;600;700&display=swap">
<style>
  :root {
    --page-bg: #ece8e1;
    --card-bg: #ffffff;
    --gold: #b59f6e;
    --gold-light: #e9e0c8;
    --burgundy: #9b1f4e;
    --grey-text: #7c7c7c;
    --leaf-orange: #e8762c;
    --leaf-amber: #f2a23a;
    --leaf-yellow: #f6c85a;
  }
  * { box-sizing: border-box; margin: 0; padding: 0; }
  html, body {
    width: 1200px; height: 950px; overflow: hidden;
    background: var(--page-bg);
    font-family: "Open Sans", Arial, sans-serif;
  }
  .card {
    position: absolute; left: 100px; top: 175px;
    width: 1000px; height: 600px;
    background: var(--card-bg);
    border-radius: 26px;
    overflow: hidden;
    box-shadow: 0 10px 30px rgba(0,0,0,.12);
  }
  .leaf-photo {
    position: absolute; left: 330px; top: 0;
    width: 670px; height: 320px;
    background:
      radial-gradient(ellipse at 70% 20%, var(--leaf-yellow) 0%, rgba(246,200,90,0) 45%),
      radial-gradient(ellipse at 40% 45%, var(--leaf-orange) 0%, rgba(232,118,44,0) 55%),
      radial-gradient(ellipse at 85% 60%, var(--leaf-amber) 0%, rgba(242,162,58,0) 50%),
      radial-gradient(ellipse at 55% 40%, rgba(242,162,58,.8) 0%, rgba(255,255,255,0) 70%);
    -webkit-mask-image: radial-gradient(ellipse at 65% 35%, #000 45%, transparent 75%);
            mask-image: radial-gradient(ellipse at 65% 35%, #000 45%, transparent 75%);
  }
  .accent-band {
    position: absolute; left: 0; top: 365px;
    width: 60px; height: 235px;
    background: var(--burgundy);
  }
  .brand {
    position: absolute; left: 40px; top: 300px;
    display: flex; align-items: center; gap: 22px;
  }
  .brand-mark {
    width: 130px; height: 130px; border-radius: 50%;
    background: var(--gold-light);
    border: 5px solid var(--gold);
    position: relative; z-index: 1;
  }
  .brand-name {
    font-weight: 300; font-size: 48px; line-height: 60px; color: var(--gold);
    letter-spacing: .5px;
  }
  .details {
    position: absolute; left: 200px; top: 405px;
    color: var(--grey-text); font-size: 18px; line-height: 24px;
  }
  .person-name { color: var(--gold); font-weight: 700; font-size: 25px; line-height: 30px; }
  .person-title { color: var(--burgundy); font-size: 19px; line-height: 26px; margin-bottom: 4px; }
  .contact { display: flex; align-items: center; gap: 10px; font-size: 16px; line-height: 22px; }
  .contact svg { width: 14px; height: 14px; fill: var(--gold); flex: none; }
</style>
</head>
<body>
  <article class="card">
    <div class="leaf-photo" role="img" aria-label="Photograph of a branch with orange and yellow autumn leaves"></div>
    <div class="accent-band"></div>

    <div class="brand">
      <div class="brand-mark"></div>
      <span class="brand-name">BrindlewayCare</span>
    </div>

    <div class="details">
      <p class="person-name">Derek Mallow</p>
      <p class="person-title">Executive Chairman</p>
      <p class="location">United Kingdom</p>
      <p class="location">Australia • New Zealand</p>
      <p class="contact">
        <svg viewBox="0 0 16 16" aria-hidden="true"><path d="M3.5 1l3 3-1.8 1.8c.8 1.9 2.6 3.7 4.5 4.5L11 8.5l3 3-2 2.5C6.5 13.5 2.5 9.5 1 4z"/></svg>
        01742 918576
      </p>
      <p class="contact">
        <svg viewBox="0 0 16 16" aria-hidden="true"><path d="M1 3h14v10H1z M1.5 3.5L8 9l6.5-5.5" fill="none" stroke="#b59f6e" stroke-width="1.6"/></svg>
        d.mallow@plumvora.example
      </p>
      <p class="contact">
        <svg viewBox="0 0 16 16" aria-hidden="true"><circle cx="8" cy="8" r="6.5" fill="none" stroke="#b59f6e" stroke-width="1.5"/><path d="M1.5 8h13M8 1.5c-3 3.5-3 9.5 0 13M8 1.5c3 3.5 3 9.5 0 13" fill="none" stroke="#b59f6e" stroke-width="1.2"/></svg>
        www.plumvora.example
      </p>
    </div>
  </article>
</body>
</html>
```